Webshop for furniture and lamps

We need a design for a web shop with APP that should have two options:
1-Webshop in general which should attract to private customer in general and
2-Website that is meant to attract big customers as hotels and restaurants who would have their own customerize login.

That's the idea behind the shop.

It should be diveded into 4 parts
vintage furniture
rattan set outdoor and indoor
lamps and
wooden wall decor

The name of the shop is loma vereda!

Please kindly make me an offer.

Reason: Dear designers, so far there hasn't been a design that really matched. Look up German web sites like www.glimmerhof-wohnen.de or www.sitzraum77.de... Haven't been convinced by designs! Sorry folks. Please submit some new ones. Kind regards Ned

```html
<!DOCTYPE html>
<html lang="en">
<head>
<meta charset="utf-8">
<title>Loma Vereda – Furniture &amp; Lamps</title>
<link rel="stylesheet" href="https://fonts.googleapis.com/css2?family=Oswald:wght@400;500;600;700&family=Open+Sans:wght@400;600;700&display=swap">
<style>
:root{
  --red:#d23a2f;
  --red-dark:#b52e25;
  --ink:#222222;
  --text:#555555;
  --muted:#8a8a8a;
  --line:#dddddd;
  --topbar:#f4f4f4;
  --wood:#3a2f2a;
  --wood-light:#4a3d36;
  --panel:#453d39;
  --panel-dark:#37302d;
  --footer:#2a2422;
  --white:#ffffff;
  --head:'Oswald',sans-serif;
  --body:'Open Sans',sans-serif;
}
*{box-sizing:border-box;margin:0;padding:0}
html,body{width:1200px;height:3214px;overflow:hidden}
body{font-family:var(--body);color:var(--text);background:var(--white);position:relative}
.wrap{width:1008px;margin:0 auto;position:relative}

/* top bar */
.topbar{height:58px;background:var(--topbar);border-bottom:1px solid #e6e6e6;font-size:13px;color:#666}
.topbar .wrap{display:flex;justify-content:space-between;align-items:center;height:100%;width:1030px}
.topbar-links{display:flex;gap:34px}

/* header */
.site-header{height:108px;border-bottom:1px solid #eee}
.site-header .wrap{display:flex;justify-content:space-between;align-items:center;height:100%;width:1030px}
.brand{display:flex;align-items:center;gap:14px;font-family:var(--head);font-weight:700;font-size:34px;color:var(--ink);letter-spacing:.5px}
.brand-mark{width:44px;height:32px;background:var(--ink)}
.main-nav{display:flex;gap:24px;align-items:center;font-family:var(--head);font-weight:500;font-size:14px;color:var(--ink);letter-spacing:.3px}

/* hero */
.hero{height:444px;position:relative;background:linear-gradient(90deg,#d9d4cc 0%,#b98a62 30%,#c99a6c 55%,#8b7c73 80%,#6f6a68 100%)}
.hero-cta{position:absolute;left:718px;top:124px;display:flex;flex-direction:column;align-items:center;width:350px}
.hero-kicker{background:var(--red);color:var(--white);font-family:var(--head);font-weight:700;font-size:32px;padding:4px 18px;letter-spacing:1px}
.hero-title{margin-top:10px;background:var(--red);color:var(--white);font-family:var(--head);font-weight:700;font-size:64px;line-height:1;padding:8px 22px;outline:3px solid var(--white);outline-offset:-9px;letter-spacing:5px}
.hero-sign{margin-top:10px;background:var(--red);color:var(--white);font-family:var(--head);font-weight:700;font-size:32px;padding:4px 40px 10px;letter-spacing:1px;clip-path:polygon(0 0,100% 0,94% 100%,6% 100%)}

/* category */
.categories{height:917px;text-align:center;padding-top:68px}
.boxed-title{display:inline-block;border:2px solid var(--ink);font-family:var(--head);font-weight:700;font-size:20px;color:var(--ink);padding:10px 28px;letter-spacing:.5px}
.cat-list{margin-top:44px;font-size:13px;color:#666;letter-spacing:.3px}
.cat-list .active{color:var(--red);font-weight:700}
.cat-list .sep{margin:0 6px}
.cat-intro{margin-top:6px;font-size:12px;color:var(--muted)}
.read-more{display:block;margin-top:22px;font-family:var(--head);font-weight:600;font-size:12px;color:var(--ink);letter-spacing:.5px}
.products{display:flex;justify-content:space-between;margin:50px auto 0;width:872px}
.product{width:268px}
.product-img{height:248px}
.product-img.one{background:linear-gradient(180deg,#fafafa 0,#fafafa 6%,#b5463a 6%,#6d8a7f 50%,#8a5a3f 94%,#fafafa 94%)}
.product-img.two{background:linear-gradient(180deg,#f4f4f4 0,#f4f4f4 30%,#9c8a6a 30%,#6f6a55 80%,#f4f4f4 80%)}
.product-img.three{background:linear-gradient(180deg,#fafafa 0,#fafafa 10%,#7a4e35 10%,#5b3a28 90%,#fafafa 90%)}
.product h3{margin-top:56px;font-family:var(--head);font-weight:600;font-size:15px;color:var(--ink)}
.product h3::after{content:"";display:block;width:30px;height:2px;background:var(--ink);margin:10px auto 0}
.price{margin-top:14px;font-family:var(--head);font-weight:600;font-size:15px;color:var(--red)}
.product p{margin-top:20px;font-size:12px;line-height:21px;color:#777}
.product p b{color:var(--ink)}
.shop-now{display:inline-block;margin-top:58px;width:236px;height:54px;line-height:54px;background:var(--red);color:var(--white);font-family:var(--head);font-weight:700;font-size:22px;clip-path:polygon(0 0,100% 0,88% 100%,12% 100%)}

/* blog */
.blog{height:763px;background:repeating-linear-gradient(90deg,var(--wood) 0,var(--wood) 90px,#3f332d 90px,#3f332d 180px);padding-top:86px;color:#d8d0cb;text-align:center}
.blog .boxed-title{border-color:var(--white);color:var(--white)}
.post-grid{display:grid;grid-template-columns:repeat(3,300px);column-gap:54px;row-gap:48px;margin:64px 0 0 96px;text-align:left}
.post-head{display:flex;align-items:center;gap:18px}
.post-num{width:44px;height:44px;background:var(--red);color:var(--white);font-family:var(--head);font-weight:700;font-size:26px;display:flex;align-items:center;justify-content:center}
.post-head h4{font-family:var(--head);font-weight:600;font-size:18px;color:var(--white)}
.post-head h4::after{content:"";display:block;width:34px;height:2px;background:var(--white);margin-top:8px}
.post p{margin-top:14px;font-size:12px;line-height:21px;color:#cfc6c0}
.post .read-more{color:var(--white);margin-top:14px}
.promo{position:absolute;left:96px;top:2162px;width:1008px;height:128px;display:flex}
.promo-img{width:540px;background:linear-gradient(90deg,#8e6e45,#c7b58c 50%,#9a8060)}
.promo-body{flex:1;background:var(--red);display:flex;align-items:center;justify-content:space-between;padding:0 46px 0 36px}
.promo-body h3{font-family:var(--head);font-weight:700;font-size:32px;color:var(--white);line-height:1.05}
.promo-body h3 small{display:block;font-size:17px;font-weight:500;letter-spacing:.5px}
.promo-btn{border:2px solid var(--white);color:var(--white);font-family:var(--head);font-weight:600;font-size:15px;padding:9px 16px}

/* testimonial & video */
.social-proof{position:absolute;top:2290px;left:0;width:1200px;height:470px}
.social-proof .boxed-title{position:absolute;top:65px;padding:12px 0;width:332px;text-align:center}
.testimonial{position:absolute;left:96px;top:183px;width:534px;height:219px;background:#f1f1f1;display:flex}
.testimonial-text{flex:1;padding:34px 22px}
.testimonial-text h4{font-family:var(--head);font-weight:600;font-size:17px;color:var(--ink)}
.testimonial-text h4::after{content:"";display:block;width:30px;height:2px;background:var(--ink);margin-top:10px}
.testimonial-text p{margin-top:16px;font-size:12px;line-height:22px;color:#777}
.testimonial-photo{width:200px;background:linear-gradient(160deg,#d8c8b8,#a78a72 60%,#e8e2dc)}
.video{position:absolute;left:678px;top:183px;width:345px;height:219px;background:linear-gradient(170deg,#5d7a52,#3a3a3a 55%,#b79b78);display:flex;align-items:center;justify-content:center}

/* features */
.features{position:absolute;top:2760px;left:0;width:1200px;height:361px;background:var(--panel-dark)}
.feature-row{display:flex;gap:2px;margin-left:96px;width:1008px}
.feature{width:334px;height:315px;background:var(--panel);text-align:center}
.feature-head{height:96px;background:var(--red);display:flex;align-items:center;justify-content:center;gap:22px;font-family:var(--head);font-weight:600;font-size:19px;color:var(--white)}
.feature:nth-child(2) .feature-head{background:var(--red-dark)}
.feature-body{padding:32px 40px 0}
.feature-body::before{content:"";display:block;width:40px;height:2px;background:#bbb;margin:0 auto 20px}
.feature-body p{font-size:12px;line-height:22px;color:#d0c8c3}
.cards{display:flex;justify-content:center;gap:12px;margin-top:12px}
.cards span{width:48px;height:28px;background:var(--white);border-radius:3px}
.feature .btn{display:inline-block;margin-top:34px;border:2px solid #d0c8c3;color:var(--white);font-family:var(--head);font-weight:600;font-size:13px;padding:6px 26px}

/* footer */
.site-footer{position:absolute;top:3121px;left:0;width:1200px;height:93px;background:var(--footer);font-size:13px;color:#bbb}
.site-footer .wrap{display:flex;align-items:center;height:100%;width:1030px}
.site-footer b{color:var(--white)}
.footer-nav{display:flex;gap:22px;margin-left:78px;color:#ddd}
.socials{display:flex;gap:10px;margin-left:auto}
.socials span{width:26px;height:26px}
</style>
</head>
<body>

<div class="topbar">
  <div class="wrap">
    <span>Mara Lindqvist, welcome to our online store!</span>
    <div class="topbar-links"><span>Login</span><span>My Account ⌄</span><span>0 item</span><span>Checkout</span></div>
  </div>
</div>

<header class="site-header">
  <div class="wrap">
    <div class="brand"><span class="brand-mark"></span>LOMA VEREDA</div>
    <nav class="main-nav">
      <span>HOME</span><span>SHOP BY BRAND</span><span>TOP SELLERS</span><span>CLEARANCE</span><span>HELP CENTER</span><span>MY FAVORITES</span>
      <svg width="14" height="14" viewBox="0 0 14 14"><circle cx="6" cy="6" r="4.5" fill="none" stroke="#222" stroke-width="2"/><line x1="9.5" y1="9.5" x2="13" y2="13" stroke="#222" stroke-width="2"/></svg>
    </nav>
  </div>
</header>

<section class="hero" role="img" aria-label="Bedroom interior with a white bed, bedside lamp and a brick wall">
  <div class="hero-cta">
    <div class="hero-kicker">ARE YOU BUSSINES</div>
    <div class="hero-title">MEMBER?</div>
    <div class="hero-sign">SIGN IN HERE</div>
  </div>
</section>

<section class="categories">
  <h2 class="boxed-title">SHOP BY CATEGORY</h2>
  <p class="cat-list">VINTAGE FURNITURE<span class="sep">|</span><span class="active">RATTAN SET OUTDOOR AND INDOOR</span><span class="sep">|</span>LAMPS<span class="sep">|</span>WOODEN WALL DECOR</p>
  <p class="cat-intro">sunt perspiciatis unde omnis iste natus error sit voluptatem accusantium doloremque laudantium totam rem aperiam eaque ipsa quae</p>
  <span class="read-more">READ MORE</span>
  <div class="products">
    <article class="product">
      <div class="product-img one" role="img" aria-label="Painted vintage chest of drawers"></div>
      <h3>VOLUPTATEM FUGIT AUT</h3>
      <div class="price">$076.00</div>
      <p>ipsum dolor sit amet <b>voluptatem</b> fugit aut ut nemo rem ipsam quia voluptatem</p>
    </article>
    <article class="product">
      <div class="product-img two" role="img" aria-label="Weathered wooden trunk"></div>
      <h3>VOLUPTATEM FUGIT AUT</h3>
      <div class="price">$076.00</div>
      <p>ipsum dolor sit amet voluptatem fugit aut ut nemo rem <b>ipsam</b> quia voluptatem</p>
    </article>
    <article class="product">
      <div class="product-img three" role="img" aria-label="Rustic wooden cabinet with an open door"></div>
      <h3>VOLUPTATEM FUGIT AUT</h3>
      <div class="price">$076.00</div>
      <p>ipsum <b>dolor sit</b> amet voluptatem fugit aut ut nemo rem ipsam quia voluptatem</p>
    </article>
  </div>
  <span class="shop-now">SHOP NOW</span>
</section>

<section class="blog">
  <h2 class="boxed-title">LATES NEWS FROM BLOG</h2>
  <div class="post-grid">
    <article class="post"><div class="post-head"><span class="post-num">1</span><h4>AMET VOLUPTATEM</h4></div><p>Lorem ipsum dolor sit amet nemo rem illo omnis aperiam ab ipsam ipsa odit aut aperiam aspernatur veritatis unde enim accusantium laudantium</p><span class="read-more">READ MORE</span></article>
    <article class="post"><div class="post-head"><span class="post-num">2</span><h4>AMET VOLUPTATEM</h4></div><p>Lorem ipsum dolor sit amet nemo rem illo omnis aperiam ab ipsam ipsa odit aut aperiam aspernatur veritatis unde enim accusantium laudantium</p><span class="read-more">READ MORE</span></article>
    <article class="post"><div class="post-head"><span class="post-num">3</span><h4>AMET VOLUPTATEM</h4></div><p>Lorem ipsum dolor sit amet nemo rem illo omnis aperiam ab ipsam ipsa odit aut aperiam aspernatur veritatis unde enim accusantium laudantium</p><span class="read-more">READ MORE</span></article>
    <article class="post"><div class="post-head"><span class="post-num">4</span><h4>AMET VOLUPTATEM</h4></div><p>Lorem ipsum dolor sit amet nemo rem illo omnis aperiam ab ipsam ipsa odit aut aperiam aspernatur veritatis unde enim accusantium laudantium</p><span class="read-more">READ MORE</span></article>
    <article class="post"><div class="post-head"><span class="post-num">5</span><h4>AMET VOLUPTATEM</h4></div><p>Lorem ipsum dolor sit amet nemo rem illo omnis aperiam ab ipsam ipsa odit aut aperiam aspernatur veritatis unde enim accusantium laudantium</p><span class="read-more">READ MORE</span></article>
    <article class="post"><div class="post-head"><span class="post-num">6</span><h4>AMET VOLUPTATEM</h4></div><p>Lorem ipsum dolor sit amet nemo rem illo omnis aperiam ab ipsam ipsa odit aut aperiam aspernatur veritatis unde enim accusantium laudantium</p><span class="read-more">READ MORE</span></article>
  </div>
</section>

<aside class="promo">
  <div class="promo-img" role="img" aria-label="Rattan outdoor sofa set with striped cushions"></div>
  <div class="promo-body">
    <h3>OUTSIDE FURNITURE<small>BIG SAVINGS ON QUALITY ITEMS</small></h3>
    <span class="promo-btn">SHOP NOW</span>
  </div>
</aside>

<section class="social-proof">
  <h2 class="boxed-title" style="left:236px">WHAT THEY SAYS</h2>
  <h2 class="boxed-title" style="left:720px;width:260px">WATCH OUR VIDEO</h2>
  <div class="testimonial">
    <div class="testimonial-text">
      <h4>THEO BRANDT, 25 YO</h4>
      <p>Lorem ipsum dolor sit amet nemo rem illo omnis aperiam ab ipsam odit aut aperiam veritatis unde enim accusantium ipsam sed dolore ...</p>
    </div>
    <div class="testimonial-photo" role="img" aria-label="Portrait photo of the customer"></div>
  </div>
  <div class="video" role="img" aria-label="Video still of rattan dining set on a wooden deck">
    <svg width="50" height="50" viewBox="0 0 50 50"><circle cx="25" cy="25" r="25" fill="#fff"/><path d="M20 15 L35 25 L20 35 Z" fill="#333"/></svg>
  </div>
</section>

<section class="features">
  <div class="feature-row">
    <div class="feature">
      <div class="feature-head">
        <svg width="30" height="30" viewBox="0 0 30 30"><rect x="3" y="7" width="24" height="17" rx="2" fill="none" stroke="#fff" stroke-width="2.5"/><rect x="3" y="11" width="24" height="3" fill="#fff"/></svg>
        PAYMENT METHOD</div>
      <div class="feature-body">
        <p>Lorem ipsum dolor sit amet omnis aperiam ab ipsam odit aut</p>
        <div class="cards"><span></span><span></span><span></span><span></span></div>
        <span class="btn">READ MORE</span>
      </div>
    </div>
    <div class="feature">
      <div class="feature-head">
        <svg width="40" height="28" viewBox="0 0 40 28"><rect x="1" y="3" width="24" height="17" fill="#fff"/><path d="M26 9 H34 L39 15 V20 H26 Z" fill="#fff"/><circle cx="9" cy="23" r="4" fill="#fff" stroke="#b52e25" stroke-width="2"/><circle cx="32" cy="23" r="4" fill="#fff" stroke="#b52e25" stroke-width="2"/></svg>
        FREE SHIPPING</div>
      <div class="feature-body">
        <p>Lorem ipsum dolor sit amet omnis aperiam ab ipsam odit aut aperiam aspernatur veritatis unde enim accusantium laudantium</p>
        <span class="btn">READ MORE</span>
      </div>
    </div>
    <div class="feature">
      <div class="feature-head">
        <svg width="26" height="32" viewBox="0 0 26 32"><path d="M6 14 V9 a7 7 0 0 1 14 0 V14" fill="none" stroke="#fff" stroke-width="3"/><rect x="2" y="14" width="22" height="17" rx="2" fill="#fff"/></svg>
        SECURE SHOPPING</div>
      <div class="feature-body">
        <p>Lorem ipsum dolor sit amet omnis aperiam ab ipsam odit aut aperiam aspernatur veritatis unde enim accusantium laudantium</p>
        <span class="btn">READ MORE</span>
      </div>
    </div>
  </div>
</section>

<footer class="site-footer">
  <div class="wrap">
    <span>© 2014 <b>YOUR COMPANY</b>. ALL RIGHTS RESERVED.</span>
    <nav class="footer-nav"><span>ABOUT US</span><span>TERM AND USE</span><span>PRIVACY POLICY</span><span>FAQS</span><span>CONTACT US</span></nav>
    <div class="socials" aria-label="Social links">
      <span style="background:#3b5998"></span><span style="background:#2fa8de"></span><span style="background:#d23a2f"></span><span style="background:#2a7bb5"></span><span style="background:#c8232c"></span>
    </div>
  </div>
</footer>

</body>
</html>
```